Landing Page Design for Adult Dating Age Verification (18+)

The objective of this task is to design a visually appealing pre-landing page for the adult dating site "Quillmera (site: https://quillmera.com/)" with an age verification mechanism. The pre-landing page will feature two buttons that redirect visitors to the main offer. The design should also include a footer block that includes links to the terms of use, privacy policy, and contact us pages.

Design Requirements:
Develop an age verification section prominently displayed on the pre-landing page.
Design the section to include two buttons labeled "Yes" and "No" for visitors to confirm their age.
Ensure the section is visually appealing and clearly communicates the purpose of age verification.

Visual Appeal:
Create a visually appealing design that aligns with the branding and theme of the "Quillmera" adult dating site.
Use suitable color schemes, typography, and graphics to enhance the overall visual appeal of the pre-landing page.

Layout and Navigation:
Design an engaging and intuitive layout that encourages visitors to interact with the page and proceed to the main offer.
Ensure clear and visible navigation elements that direct visitors to the main offer or provide additional information.

Responsive Design:
Develop a responsive design that provides a seamless user experience across various devices, including desktop and mobile.
Ensure the design elements and layout adapt well to different screen sizes and resolutions.

File Formats and Assets:
Deliver the final design in PSD, AI, or Sketch format, ensuring that the files are well-organized and layered.
Include any necessary images or assets used in the design, ensuring they are of high quality and optimized for web use.

```html
<!DOCTYPE html>
<html lang="en">
<head>
<meta charset="utf-8">
<title>Quillmera – Age Verification</title>
<link rel="stylesheet" href="https://fonts.googleapis.com/css2?family=Rozha+One&family=Source+Sans+3:wght@400;700&display=swap">
<style>
  :root {
    --page-bg: #d7badb;
    --lilac: #d3b3d6;
    --night: #1b1a22;
    --night-soft: #3a3944;
    --white: #ffffff;
    --red: #ff2b2b;
    --display: "Rozha One", Georgia, serif;
    --sans: "Source Sans 3", Arial, sans-serif;
  }
  * { box-sizing: border-box; margin: 0; padding: 0; }
  html, body { width: 1200px; height: 1040px; overflow: hidden; }
  body { background: var(--page-bg); font-family: var(--sans); position: relative; }

  .view-label {
    position: absolute; top: 258px;
    color: var(--white); font-family: var(--sans); font-weight: 400;
    font-size: 16px; letter-spacing: 0.2px;
  }
  .view-label--mobile { left: 44px; }
  .view-label--desktop { left: 328px; }

  .screen {
    position: absolute; top: 303px; overflow: hidden;
    background: var(--night);
    box-shadow: 0 6px 16px rgba(60, 30, 70, 0.35);
  }
  .screen--mobile { left: 44px; width: 246px; height: 478px; }
  .screen--desktop { left: 328px; width: 820px; height: 476px; }

  .status-bar {
    position: absolute; top: 0; left: 0; right: 0; height: 15px;
    background: #111; color: var(--white); font-size: 8px;
    display: flex; align-items: center; justify-content: space-between; padding: 0 6px;
  }
  .status-bar__battery { display: flex; align-items: center; gap: 3px; }
  .status-bar__battery span { display: inline-block; width: 18px; height: 7px; border: 1px solid #fff; padding: 1px; }
  .status-bar__battery span::after { content: ""; display: block; height: 100%; background: #fff; }

  .hero-photo {
    position: absolute; left: 0; right: 0; top: 0;
    background:
      radial-gradient(ellipse 40% 35% at 45% 40%, rgba(120,118,132,0.55), transparent 70%),
      radial-gradient(ellipse 45% 40% at 75% 55%, rgba(100,98,112,0.45), transparent 70%),
      linear-gradient(135deg, #15141b 0%, #2d2c36 50%, #17161d 100%);
  }
  .screen--mobile .hero-photo { top: 15px; height: 412px; }
  .screen--desktop .hero-photo { height: 433px; }

  .gate {
    position: absolute; left: 0; right: 0; text-align: center; color: var(--white);
  }
  .brand {
    display: flex; align-items: center; justify-content: center; gap: 6px;
    font-family: var(--display); font-weight: 400; color: var(--white); line-height: 1;
  }
  .brand__dot { border-radius: 50%; background: var(--lilac); display: inline-block; }
  .gate__icon { display: block; margin: 0 auto; }
  .gate__title { font-family: var(--display); font-weight: 400; line-height: 1.1; }
  .gate__note { font-weight: 400; }
  .gate__actions { display: flex; justify-content: center; }
  .btn {
    display: inline-flex; align-items: center; justify-content: center;
    border-radius: 999px; font-weight: 700; color: var(--white); text-decoration: none;
    letter-spacing: 0.2px;
  }
  .btn--over { background: var(--red); }
  .btn--under { border: 1px solid var(--white); }

  .footer-links {
    position: absolute; left: 0; right: 0; bottom: 0; background: var(--lilac);
    display: flex; align-items: center; justify-content: center;
  }
  .footer-links a { color: var(--white); text-decoration: none; text-transform: uppercase; }

  /* mobile */
  .screen--mobile .gate { top: 46px; }
  .screen--mobile .brand { font-size: 22px; }
  .screen--mobile .brand__dot { width: 18px; height: 18px; }
  .screen--mobile .gate__icon { margin-top: 36px; width: 40px; height: 46px; }
  .screen--mobile .gate__title { font-size: 23px; margin-top: 6px; line-height: 1.25; }
  .screen--mobile .gate__note { font-size: 13px; margin-top: 12px; }
  .screen--mobile .gate__actions { gap: 8px; margin-top: 16px; }
  .screen--mobile .btn { width: 88px; height: 22px; font-size: 9px; }
  .screen--mobile .footer-links {
    height: 51px; flex-direction: column; gap: 1px;
  }
  .screen--mobile .footer-links a { font-size: 6.5px; letter-spacing: 1.6px; }

  /* desktop */
  .screen--desktop .gate { top: 32px; }
  .screen--desktop .brand { font-size: 36px; gap: 10px; }
  .screen--desktop .brand__dot { width: 26px; height: 26px; }
  .screen--desktop .gate__icon { margin-top: 64px; width: 42px; height: 48px; }
  .screen--desktop .gate__title { font-size: 27px; margin-top: 4px; line-height: 1.2; }
  .screen--desktop .gate__note { font-size: 15px; margin-top: 6px; }
  .screen--desktop .gate__actions { gap: 10px; margin-top: 16px; }
  .screen--desktop .btn { width: 98px; height: 24px; font-size: 10px; }
  .screen--desktop .footer-links { height: 43px; gap: 60px; }
  .screen--desktop .footer-links a { font-size: 11.5px; letter-spacing: 3px; }
</style>
</head>
<body>
  <p class="view-label view-label--mobile">MOBILE VIEW</p>
  <p class="view-label view-label--desktop">DESKTOP VIEW</p>

  <section class="screen screen--mobile" aria-label="Quillmera age check, mobile">
    <div class="status-bar">
      <span>●●●●○</span>
      <span>2:56 PM</span>
      <span class="status-bar__battery">100% <span></span></span>
    </div>
    <div class="hero-photo" role="img" aria-label="Dim black and white photograph of an embracing couple"></div>
    <div class="gate">
      <div class="brand"><span class="brand__dot"></span>Quillmera</div>
      <svg class="gate__icon" viewBox="0 0 40 46" aria-hidden="true" fill="none" stroke="#fff" stroke-width="1.6">
        <circle cx="13" cy="23" r="9"/>
        <circle cx="22" cy="17" r="9"/>
        <line x1="13" y1="32" x2="13" y2="43"/><line x1="8" y1="38" x2="18" y2="38"/>
        <line x1="28.5" y1="10.5" x2="36" y2="3"/><polyline points="30,3 36,3 36,9"/>
      </svg>
      <h1 class="gate__title">The site contains<br>sexually explicit<br>material.</h1>
      <p class="gate__note">Enter ONLY if you are over 18</p>
      <div class="gate__actions">
        <a class="btn btn--over" href="https://quillmera.com/">I AM OVER 18</a>
        <a class="btn btn--under" href="#">I AM UNDER 18</a>
      </div>
    </div>
    <nav class="footer-links">
      <a href="#">Terms of use</a><a href="#">Privacy policy</a><a href="#">Contact us</a>
    </nav>
  </section>

  <section class="screen screen--desktop" aria-label="Quillmera age check, desktop">
    <div class="hero-photo" role="img" aria-label="Dim black and white photograph of an embracing couple"></div>
    <div class="gate">
      <div class="brand"><span class="brand__dot"></span>Quillmera</div>
      <svg class="gate__icon" viewBox="0 0 40 46" aria-hidden="true" fill="none" stroke="#fff" stroke-width="1.6">
        <circle cx="13" cy="23" r="9"/>
        <circle cx="22" cy="17" r="9"/>
        <line x1="13" y1="32" x2="13" y2="43"/><line x1="8" y1="38" x2="18" y2="38"/>
        <line x1="28.5" y1="10.5" x2="36" y2="3"/><polyline points="30,3 36,3 36,9"/>
      </svg>
      <h1 class="gate__title">The site contains sexually<br>explicit material.</h1>
      <p class="gate__note">Enter ONLY if you are over 18</p>
      <div class="gate__actions">
        <a class="btn btn--over" href="https://quillmera.com/">I AM OVER 18</a>
        <a class="btn btn--under" href="#">I AM UNDER 18</a>
      </div>
    </div>
    <nav class="footer-links">
      <a href="#">Terms of use</a><a href="#">Privacy policy</a><a href="#">Contact us</a>
    </nav>
  </section>
</body>
</html>
```